Tradlo - Forex Signal Services Moments Matter Most. Reshape your path.

I need an attractive eye catching web design that is azure friendly. I currently have a web programmer working on the backend of my website. Now I need a professional design to attract and retain customers. This site needs to be mobile friendly.

Tradlo is a highly reputable, trustworthy and professional site that offers forex signals to traders in all parts of the globe. With accurate and reliable forex signals, traders can not only make money but also boost their profits.

At Tradlo, we want our clients to have complete faith on us and our services! We also do not want our users to lead a simple and monotonous life. Instead our goal is to help them create an extra source of steady income. However, this is possible only when our clients resolve to change their lives for the better. They need to change their mindset and most importantly develop a positive frame of mind. That’s exactly why at Tradlo, we provide our clients with innumerable personal development tools and resources that’ll aid them in changing all the aspects of their lives. We want our traders to feel inspired and educate them in the right way!

Colors are flexible.

I do like the simplicity of www.brightmarkvo.example.
I do want a design more professional in appearance and not everything on page one.

I have not been able to decide on a logo. There is one of lower quality as I have not paid for it yet but I will if you decide it's the best for my business I will. Or should one feel that they have a better idea for a logo, I will pay for it if i like it.

I have included some of the content of my site so you can get a feel for where I am coming from.
(Please note that this content is still in the editing process)
Updates

Project Deadline Extended Reason: My content was not complete nor finalization of the final logo. We will allow a few more days for designers to modify the website.Thank you for your patience and understanding. Added Tuesday, January 24, 2017

Target Market(s)

I work with Forex Traders, Investors wanting to control their own portfolios, and remote nomads/mellienials

Coding

Coded - Design and coding required

Number of Pages Required

5+ page

Requirements
Must have
• I must have a professional clean look. I want the site to be interactive and eye catching. I want my audience hooked within seconds of opening it. It has to have all important information first. Photos must be legit and not spammy. I work as a representative in the financial market. I want my site to reflect that I stand by my product and reputation means everything to me. This site has to be engaging.
• Sorry, I should have included this earlier of what I will all need on this site.
• I'll have about Tradlo (my company, what we stand for, who we work with, my strategy, etc....
• about me (why i started this company, who I am)
• Performance (graphs and recent posts of signals)
• Membership (how to sign up)
• Terms of service/legal/disclaimers
• FAQS
• Personal Development Resources
• Forex Education Resources
Nice to have
• Quick links to bounce around the site faster.
Should not have
• I do not want over the top white collar conservative.

```html
<!DOCTYPE html>
<html lang="en">
<head>
<meta charset="utf-8">
<title>Tradlo - Forex Signal Services</title>
<link rel="stylesheet" href="https://fonts.googleapis.com/css2?family=Oswald:wght@500;600&family=Open+Sans:wght@400;600;700&family=Raleway:wght@300;400;600&display=swap">
<style>
:root{
  --orange:#e8561b;
  --orange-dark:#c94512;
  --ink:#1b1b1b;
  --night:#111417;
  --paper:#efedeb;
  --text:#333;
  --white:#fff;
  --line:#c9c6c3;
}
*{box-sizing:border-box;margin:0;padding:0}
html,body{width:1200px;height:3352px;overflow:hidden}
body{position:relative;font-family:"Open Sans",Arial,sans-serif;color:var(--text);background:var(--paper);font-size:12px;line-height:1.45}
.section{position:absolute;left:0;width:1200px;text-align:center;overflow:hidden}
.bg{position:absolute;inset:0}
.content{position:relative;width:760px;margin:0 auto}

/* header */
.site-header{position:absolute;top:0;left:235px;width:737px;height:78px;background:var(--white);display:flex;align-items:center;z-index:5;box-shadow:0 2px 6px rgba(0,0,0,.25)}
.brand{width:110px;height:78px;display:flex;align-items:center;justify-content:center;gap:6px;border-right:1px solid #eee;font-weight:700;font-size:17px;color:var(--ink)}
.brand-dot{width:14px;height:14px;border-radius:50%;background:var(--orange)}
.main-nav{display:flex;flex:1;justify-content:space-around;padding:0 8px}
.main-nav a{font-size:10.5px;font-weight:600;color:var(--ink);text-decoration:none;text-transform:uppercase;padding:6px 0}
.main-nav a.active{color:var(--orange);border-bottom:2px solid var(--orange)}

/* hero */
.hero{top:0;height:615px;color:var(--white)}
.hero .bg{background:linear-gradient(180deg,#1c2126 0%,#2c2a28 45%,#5a3820 75%,#2b1c14 100%)}
.hero-title{position:absolute;top:195px;left:0;width:1200px;font-family:"Oswald",Arial,sans-serif;font-weight:600;font-size:66px;letter-spacing:2px;line-height:1}
.hero-sub{position:absolute;top:250px;left:0;width:1200px;font-family:"Oswald",Arial,sans-serif;font-size:30px;letter-spacing:24px;line-height:1}
.hero-text{position:absolute;top:272px;left:400px;width:400px;font-size:13px;line-height:1.3}
.slide-arrow{position:absolute;top:230px;width:30px;height:56px;background:rgba(60,60,60,.7);display:flex;align-items:center;justify-content:center}
.slide-arrow.prev{left:0}.slide-arrow.next{right:0}

.feature-row{position:absolute;top:454px;left:217px;display:flex;z-index:3}
.feature{width:255px;height:161px;padding:22px 18px 0;color:var(--white);text-align:center;background:var(--orange)}
.feature.dark{background:var(--ink)}
.feature h3{font-family:"Raleway",Arial,sans-serif;font-weight:600;font-size:16px;letter-spacing:1px;margin:10px 0 6px;text-transform:uppercase}
.feature p{font-size:9.5px;font-weight:600;line-height:1.35}

/* headings */
.title-orange{font-family:"Raleway",Arial,sans-serif;font-weight:600;font-size:30px;letter-spacing:7px;color:var(--orange);text-transform:uppercase}
.title-light{font-family:"Raleway",Arial,sans-serif;font-weight:300;font-size:34px;letter-spacing:5px;color:var(--white)}
.sub-head{font-weight:700;font-size:13.5px;letter-spacing:1px;color:var(--ink);text-transform:uppercase;margin:16px 0 10px}
.body-copy{font-size:11px;line-height:1.38;color:var(--text)}
.on-dark .body-copy{color:#f3f3f3}
.btn-outline{display:inline-block;margin-top:20px;padding:6px 26px;border:1px solid var(--orange);color:var(--orange);font-size:11px;text-transform:uppercase;letter-spacing:1px;background:rgba(255,255,255,.4)}
.btn-light{display:inline-block;margin-top:20px;padding:6px 22px;border:1px solid var(--white);color:var(--white);font-size:12px}

.welcome{top:615px;height:364px}
.welcome .bg{background:linear-gradient(180deg,#f1efed,#e7e3e0)}
.welcome .content{padding-top:45px}

.advantage{top:979px;height:273px}
.advantage .bg{background:linear-gradient(100deg,#e05a1f 0%,#e8561b 50%,#d9481a 100%)}
.advantage .content{padding-top:45px}
.advantage .body-copy{margin-top:18px;color:#fde7dc}

.strategy{top:1252px;height:335px}
.strategy .bg{background:linear-gradient(180deg,#efedeb,#e5e1dd)}
.strategy .content{padding-top:36px}
.strategy .body-copy{margin-top:22px}
.strategy .body-copy p+p{margin-top:10px}

.why{top:1587px;height:273px}
.why .bg{background:linear-gradient(180deg,#16191c,#202428 60%,#15181a)}
.why .content{padding-top:38px}
.why .body-copy{margin-top:18px}

.reasons{top:1860px;height:335px}
.reasons .bg{background:linear-gradient(180deg,#efedeb,#e6e2de)}
.reasons .content{padding-top:30px}
.reasons .title-orange{font-size:28px}
.reasons .body-copy{margin-top:14px}
.channels{display:flex;justify-content:center;gap:18px;margin:6px 0 14px}
.channel{width:46px;height:46px;border-radius:50%;background:var(--ink);color:var(--white);font-size:10px;display:flex;align-items:center;justify-content:center}
.channel.hot{color:var(--white);box-shadow:inset 0 0 0 2px var(--orange)}

.what{top:2195px;height:270px}
.what .bg{background:linear-gradient(100deg,#e3561c,#ea5a1c 50%,#d74a18)}
.what .content{padding-top:38px}
.what .body-copy{margin-top:14px;color:#fde7dc}

/* FAQ */
.faq{top:2465px;height:441px}
.faq .bg{background:linear-gradient(180deg,#eeecea,#e4e0dc)}
.faq-title{position:absolute;top:36px;left:0;width:1200px;font-family:"Raleway",Arial,sans-serif;font-weight:600;font-size:34px;letter-spacing:9px;color:var(--orange)}
.faq-col{position:absolute;top:0;text-align:left}
.faq-col.left{left:235px;width:342px}
.faq-col.right{left:626px;width:340px}
.faq-item{position:absolute;left:0;width:100%;display:flex;align-items:center;gap:12px;font-size:10px;font-weight:600;color:var(--ink);padding-bottom:10px;border-bottom:1px solid var(--line)}
.faq-item .mark{width:12px;height:12px;background:var(--ink);flex:none;display:flex;align-items:center;justify-content:center}
.faq-item.open{color:var(--orange);border-bottom:none}
.faq-item.open .mark{background:var(--orange)}
.faq-answer{position:absolute;left:0;top:140px;width:100%;font-size:8.4px;line-height:1.38;color:#444;padding-bottom:18px;border-bottom:1px solid var(--line)}

/* contact */
.contact{top:2906px;height:413px;color:var(--white)}
.contact .bg{background:linear-gradient(180deg,#0f1215,#181c20 60%,#101316)}
.contact-title{position:absolute;top:35px;left:0;width:1200px;font-family:"Raleway",Arial,sans-serif;font-weight:600;font-size:28px;letter-spacing:7px}
.contact-info{position:absolute;top:127px;left:239px;width:220px;text-align:left;font-size:10.5px;line-height:1.4}
.phone{font-size:27px;font-weight:700;color:var(--orange);margin-top:10px;letter-spacing:1px}
.stay{margin-top:24px;font-family:"Raleway",Arial,sans-serif;font-weight:600;font-size:17px;letter-spacing:3px;color:var(--orange);text-transform:uppercase}
.social{display:flex;gap:6px;margin-top:10px}
.social span{width:44px;height:44px;border-radius:4px;background:#3a3f45;border:1px solid #575d63}
.social span:nth-child(odd){background:var(--orange);border-color:var(--orange)}
.contact-form{position:absolute;top:130px;left:487px;width:479px;text-align:left}
.field-row{display:flex;gap:28px;margin-bottom:20px}
.field{flex:1;height:38px;border-bottom:1px solid #4b4f54;border-top:2px solid var(--orange);padding:4px 4px;font-size:10px;color:#9aa0a6;background:rgba(255,255,255,.03)}
.field.area{height:98px}
.send{position:absolute;top:243px;right:0;width:110px;height:34px;background:var(--orange);color:var(--white);font-size:10px;display:flex;align-items:center;justify-content:center;letter-spacing:1px}

.site-footer{position:absolute;top:3319px;left:0;width:1200px;height:33px;background:var(--orange);color:var(--white);font-size:9.5px;font-weight:600}
.site-footer .copy{position:absolute;left:240px;top:9px}
.site-footer .top{position:absolute;left:883px;top:9px}
</style>
</head>
<body>

<header class="site-header">
  <div class="brand"><span class="brand-dot"></span>Tradlo</div>
  <nav class="main-nav">
    <a class="active">Home</a><a>Tradlo Advantage</a><a>Our Strategy</a><a>Why Tradlo</a><a>Reasons to Chose Signals</a><a>What We Do</a><a>FAQ</a><a>Contact</a>
  </nav>
</header>

<section class="section hero">
  <div class="bg" role="img" aria-label="Photo of a trading screen with glowing currency quotes and price figures"></div>
  <div class="hero-title">FOREX SIGNAL</div>
  <div class="hero-sub">SERVICES</div>
  <p class="hero-text">Tradlo.com works with both day as well as intraday traders. We only hold a maximum of one position at any given point in time. Once we've placed an order we do not move SL or TP targets.</p>
  <div class="slide-arrow prev"><svg width="12" height="20" viewBox="0 0 12 20"><path d="M10 2 2 10l8 8" fill="none" stroke="#fff" stroke-width="2"/></svg></div>
  <div class="slide-arrow next"><svg width="12" height="20" viewBox="0 0 12 20"><path d="M2 2l8 8-8 8" fill="none" stroke="#fff" stroke-width="2"/></svg></div>
  <div class="feature-row">
    <div class="feature">
      <svg width="40" height="36" viewBox="0 0 40 36" fill="#fff"><circle cx="14" cy="20" r="9"/><circle cx="14" cy="20" r="3.5" fill="#e8561b"/><rect x="12" y="8" width="4" height="24"/><rect x="2" y="18" width="24" height="4"/><circle cx="30" cy="10" r="6"/><circle cx="30" cy="10" r="2.2" fill="#e8561b"/></svg>
      <h3>The Tradlo Advantage</h3>
      <p>Delivering high-probability forex signals to help you beat the market. Accurate and reliable forex signals to take your trading</p>
    </div>
    <div class="feature dark">
      <svg width="40" height="36" viewBox="0 0 40 36" fill="#fff"><rect x="4" y="24" width="6" height="10"/><rect x="13" y="18" width="6" height="16"/><rect x="22" y="12" width="6" height="22"/><path d="M3 18 14 9l6 5 14-11" fill="none" stroke="#fff" stroke-width="2.5"/></svg>
      <h3>Tradlo Philosophy</h3>
      <p>Capital protection is the key to consistent profitability and equity growth, flexibility and taking advantage of opportunities when they arise.</p>
    </div>
    <div class="feature">
      <svg width="40" height="36" viewBox="0 0 40 36" fill="none" stroke="#fff" stroke-width="3"><rect x="12" y="3" width="18" height="30"/><path d="M2 18h16M12 12l6 6-6 6"/></svg>
      <h3>Tradlo Free Trial</h3>
      <p>Free forex signals for 30 days, trading signals to help you beat the forex market.</p>
    </div>
  </div>
</section>

<section class="section welcome">
  <div class="bg" role="img" aria-label="Faded background photo of price quote boards"></div>
  <div class="content">
    <h2 class="title-orange">Welcome to Tradlo</h2>
    <h4 class="sub-head">Moments matter most. Reshape your path</h4>
    <p class="body-copy">We use proven strategies to help traders in succeeding in the forex market. Our forex experts provide high-probability, professional and consistent forex signals and charts that help traders in maximizing their profits and eliminating losses. Try our free Currency Education service to find out what differentiates us from our competitors and how we can aid you in becoming a professional trader!</p>
    <h4 class="sub-head">What is your trading philosophy and style?</h4>
    <p class="body-copy">We follow naked forex trading techniques including price action, immediate trend and personalized mathematical formulas. Our success stems from our strict enforcement of discipline, patience, attitude, economics and timing to help our traders maximize their gains from forex trading. Obviously we do not always win, but our winning trades exceed those that are not and our take profit target is always bigger than our stop loss. We look at multiple time frames to quality setups that define our trading edge. We pay close to the London market and our entries are often based off of the 1-hour chart.</p>
  </div>
</section>

<section class="section advantage on-dark">
  <div class="bg" role="img" aria-label="Orange tinted photo of a hand over a rising trend line"></div>
  <div class="content">
    <h2 class="title-light">The Tradlo Advantage</h2>
    <p class="body-copy">Clear entries, firm exits and a steady plan give each member a real edge in a fast market. Every signal is checked against trend, timing and risk before it reaches you, so you know where to act and when to wait. We keep the rules simple, the targets honest and the updates quick, helping you trade with calm and care. Our team watches the key sessions daily and shares only setups we would take ourselves.</p>
    <span class="btn-light">Tradlo Advantage</span>
  </div>
</section>

<section class="section strategy">
  <div class="bg" role="img" aria-label="Faded background photo of currency rate displays"></div>
  <div class="content">
    <h2 class="title-orange">Our Strategy</h2>
    <div class="body-copy">
      <p>Tradlo.com works with both day as well as intraday traders. We only hold a maximum of one position at any given point in time. Once we've placed an order we do not move SL or TP targets. We follow naked forex trading techniques including price action, immediate trend and personalized mathematical formulas.</p>
      <p>Our success stems from our strict enforcement of discipline, patience, attitude, economics and timing to help our traders maximize their gains from forex trading.) At Tradlo, we trade GBP/USD, EUR/USD, AUD/USD, USD/CHF and USD/JPY pairs only and target anywhere between 25-50 pips a day with a risk/reward ratio of at least 2:1.</p>
      <p>At Tradlo.com, we aspire to become one of the most reputable and fastest growing forex signal service providing platform to traders around the world! If you're tired of your 9-5 job or need an alternate source of income, then don't look any further! We'll help you in acquiring a consistent income and a building a bright future through forex trading</p>
    </div>
    <span class="btn-outline">Read More</span>
  </div>
</section>

<section class="section why on-dark">
  <div class="bg" role="img" aria-label="Dark photo of a trader's desk with chart monitors"></div>
  <div class="content">
    <h2 class="title-light">Why Tradlo</h2>
    <p class="body-copy">Put simply, because we're different! We are a 'Never before Seen' forex trading company that is focused on guiding, mentoring and assisting traders in every possible manner! We provide tools, resources and technology that allow traders to fulfill their trading aspirations and achieve success. We trade four days a week only. Tuesday to Friday (note only trade 4 days a week Tuesday to Friday) and daily signals are sent to traders only if they meet our requisite rules and regulations. Pending order signals are generally issued by around 8:30 EST time.</p>
    <span class="btn-light">Why Tradlo</span>
  </div>
</section>

<section class="section reasons">
  <div class="bg" role="img" aria-label="Faded background photo of stock tickers"></div>
  <div class="content">
    <h2 class="title-orange">Reasons to Chose Signals</h2>
    <p class="body-copy">A few days prior to your free trial's expiration you will receive an email from us letting you know that the free service is about to be discontinued with directions on how to subscribe to our service.Forex Trading is all about speculating where the market will go next and knowing when to place a trade is key to your success.</p>
    <h4 class="sub-head">Signals are sent to our subscribers through these methods:</h4>
    <div class="channels">
      <span class="channel">SMS</span><span class="channel hot">Social</span><span class="channel">Email</span><span class="channel hot">App</span>
    </div>
    <p class="body-copy">We appeal to Forex Traders, Investors Interested in Managing their own portfolios, Remote Nomads, Work from home entrepreneurs and Mellenials Forex Traders Everywhere Forex Trading is not for the faint-hearted.</p>
    <span class="btn-outline">Read More</span>
  </div>
</section>

<section class="section what on-dark">
  <div class="bg" role="img" aria-label="Orange tinted photo of a hand writing on a glass board"></div>
  <div class="content">
    <h2 class="title-light">What We Do</h2>
    <p class="body-copy">We offer speedy, consistent, accurate and desired results. We're a highly dependable and trusted forex trading platform. Our motto is to 'Change Your World' and also to ensure that you earn profits on a regular basis.Our objective is to provide global access to trusted forex signals.Our services are highly affordable. We offer High Probable forex strategies with high rewards.We set transparent entry price and exit levels. Our team will constantly update you regarding the status of your trade till the time it is closed.</p>
    <span class="btn-light">What WE Do</span>
  </div>
</section>

<section class="section faq">
  <div class="bg" role="img" aria-label="Faded photo of a price board on the left edge"></div>
  <h2 class="faq-title">FAQ</h2>
  <div class="faq-col left">
    <div class="faq-item open" style="top:110px"><span class="mark"><svg width="8" height="8" viewBox="0 0 8 8"><path d="M1 1l6 6M7 1 1 7" stroke="#fff" stroke-width="1.5"/></svg></span>How many pips can I make per month following your signals?</div>
    <p class="faq-answer">Our view is simple. Trading is a business and not for the faint of heart. We strive to achieve 150-250 real quality pips a month. More importantly, we're much more concerned with protecting your capital and minimizing our drawdown than we are with generating more pips under far more risky conditions. We stick to our strategy and their prerequisite rules. It is also worth noting that it is not necessary to be profitable every month in order to be a profitable trader. Drawdowns are a fact of the trading life and our aim is to make them as small as we can even if it means that we'll have to pass the same extra pips. For psychological reasons it is easier to tolerate smaller drawdowns with smaller gains than larger drawdowns with larger gains.</p>
    <div class="faq-item" style="top:288px"><span class="mark"></span>Can I follow your signals and have a full time job?</div>
    <div class="faq-item" style="top:337px"><span class="mark"></span>How will I receive my signals?</div>
    <div class="faq-item" style="top:389px"><span class="mark"></span>What happens after my trial period access?</div>
  </div>
  <div class="faq-col right">
    <div class="faq-item" style="top:136px"><span class="mark"></span>How Will FOREX Signals Help You?</div>
    <div class="faq-item" style="top:188px"><span class="mark"></span>What we are not or should I say what we are?</div>
    <div class="faq-item" style="top:239px"><span class="mark"></span>How many pips can I make per month following your signals?</div>
    <div class="faq-item" style="top:292px"><span class="mark"></span>Don't need special requirements to earn money from my system?</div>
    <div class="faq-item" style="top:344px"><span class="mark"></span>Who do we serve?</div>
    <div class="faq-item" style="top:389px"><span class="mark"></span>How many pips can I make per month following your signals?</div>
  </div>
</section>

<section class="section contact">
  <div class="bg" role="img" aria-label="Dark photo of a laptop showing a trading chart"></div>
  <h2 class="contact-title">CONTACT US</h2>
  <div class="contact-info">
    <p>If you would like to get in contact with us, please fill in the form and we will get back to you as soon as we can.</p>
    <p style="margin-top:8px">Alternatively you can call us on</p>
    <div class="phone">0800 555 0142</div>
    <div class="stay">Stay Connected</div>
    <div class="social"><span></span><span></span><span></span><span></span></div>
  </div>
  <form class="contact-form">
    <div class="field-row"><div class="field">Name</div><div class="field">Email</div></div>
    <div class="field-row"><div class="field">Telephone</div><div class="field">Subject</div></div>
    <div class="field-row"><div class="field area">Message</div></div>
    <div class="send">SEND</div>
  </form>
</section>

<footer class="site-footer">
  <span class="copy">2017 © TRADLO ALL RIGHTS RESERVED.</span>
  <span class="top">BACK TO TOP</span>
</footer>

</body>
</html>
```